UI design for an Zyn(Halvo) photo editing app

This design contest is to design the UI/screenshots of an Zyn(Halvo) app named "Kestrel Pix". Some minor design details are left out at this point as the mockup is still in progress. The icon of this app will be designed separately. The winner of this job will be selected to work on a long term basis as an Dorvo version and several updates will have to be designed as well as the Quillex version. Please take
this as a long term opportunity.
The photo app is called "Kestrel Pix". The design need to dynamic, different that stands out WITH a serious and polished look.
All the mockups and sample screenshots are attached for ease. Please thoroughly review them.
This app has the following screens:
1. Welcome screen(just a simple background will do now as icon will be put later).
2. Main Screen (or LightBox)
The background of this screen can be the same as the background of the welcome screen. It can be a wooden background OR a background of your
choice that fits and blends in the buttons and fonts/colors.
The main screen has this bars/buttons/options that has separate screens:
On top, menu bar:
has these buttons
settings on the left(icon)
in the middle, 3 buttons (please check lightbox mockup and lightbox sample pics)
on the right, share icon(check share screen sample)
Our share options:
"Share" button screenshot:
Our share options:
Save
Email
Copy
Moodlefy
Chatterbay
Zorbly
Quorra
in the middle, just background where the pictures would appear later after importing
or saving
at the bottom bar:
3 buttons:
Camera Roll(on the left)
Camera Button(middle)
Advanced Button(on the right)
2 versions of this screenshot need to be designed.
1. regular version with all the options
2. regular version plus the "steam effect" button showing up on top of the "Advanced" button(mockup with red lines)
3 separate screenshots need to be designed for the options"
settings screenshot(please check sample):
Gift Kestrel Pix to a friend
Rate/review in the Tundle Hub
(space in between...so they are grouped)
Geotagiing(on/off)
Captured photos get location-specific information(these lines in smaller fonts)
Launch in Capture Mode(on/off)
Kestrel Pix is automatically lauched in camera mode
Autosave to Camera Roll(on/off)
Captured photos are directly saved to camera roll
Reset All Tutorials
Tap to reset all the tutorials
In the "Steam Effect" screen, please check the mockup
Top Bar: lightbox button(to go back), heading and Done button
Middle: Steam background(provided)
Bottom bar:
refresh button
droplets(when clicked on/off options show up on top, please check mockup)
finger size(when clicked 3 options show up)
steam density(when clicked 3 options show up)
Please use the buttons for the droplets, finger size and steam density from the steam effects button image provided)
(and also the background of this screenshot(in the middle) would be a steam screen which is provided. Please use the
steam background provided and you need to use the background in the middle, just omit the top and the bottom bar from the image)
Now back to the main(lightbox screen):
When Clicked on the "Camera" in the middle of the bottom bar, the capture mode screen shows up.
Please refer to the mockup first
There you will see the cancel button on the left
camera button in the middle
a small settings button on the right
and a filters button on the right
and the filters bar on the top
ours need to like this
please refer to capture mode sample 1
please refer to capture mode sample 2
please refer to capture mode sample 3
normal
Grid
timer(5/15/30 secs)
Edit Screen(check sample)
Edit options
Adjust:(displayed on a bar)
1. Left
2. Right
3. Horizontal
4. Vertical
5. Straightening
Crop:
None
Original
Golden
Freeform
Square
3:2
4:3
4:6
5:7
8:10
16:9
Filters:(please note that this filter icon and the filter icon in the "capture mode" screenshot need to same)
(the filters are displayed on a bar, please check sample)
There is a sample picture that you need to put in the picture of the filters. It would be same picture in
every filter at this point.
00.None
0.Calibrate
1. aurora
2. drizzle
3. icicle
4. blizzard
5. calm
6. dew
7. knot
8. dry
9. eye
10. flurry
11. fog
12. frost
13. hail
14. haze
15. heat
16. humid
17. overcast
18. polar
19. thermal
20. trace
Editing options on top:(check sample)
Brightness
Contrast
Saturation
Textures:(dispalyed on a bar, check sample)
1.None
2.Bark
3.Grunge1
4.Grunge2
5.grunge3
6.Grunge4
7.Paper
8.Cardboard
9.Wood
10.Bokeh
11.Bricks
12.Metal
13.Asphalt
14.Pavement1
15.Pavement2
16.Paint1
17.Paint2
18.Rust
19.Towel
20.Stone1
21.Stone2
22.Wall
23.Urban1
24.Urban2
25.Urban3
26.Watercolor
Tilt-shift/Vignette:(check sample)
Borders:(check samples, at this point, we are working on them, you just need to make a bar that displays them)
1.None
2.
3.
4.
5.
6.
7.
8.
9.
10.
11.
12.
13.
14.
15.
16.
This is our primary design mockup. Upon selecting the final version, we will be working on some more and minor details(as
we are also working with the coders).
And there is a folder callled "app sample". Please take a look at it and think how our app can be different and stand out.
Thanks and feel free to contact me anytime if you have any questions. Looking forward to hearing from you and building a long term
relationship.
All camera app users who likes to edit their photos with cool tools.
Building

```html
<!DOCTYPE html>
<html lang="en">
<head>
<meta charset="utf-8">
<title>Kestrel Pix – Settings</title>
<link href="https://fonts.googleapis.com/css2?family=Ubuntu:wght@400;500;700&display=swap" rel="stylesheet">
<style>
  :root {
    --status-bg: #000000;
    --status-fg: #d8d8d8;
    --nav-top: #0e8f92;
    --nav-bottom: #05686b;
    --nav-btn: #0a7a7d;
    --nav-btn-edge: #045557;
    --screen-bg: #333333;
    --divider-dark: #222222;
    --divider-light: #404040;
    --text: #ffffff;
    --text-muted: #1d1d1d;
    --toggle-on: #0b7f82;
    --toggle-off: #1e1e1e;
    --toggle-off-text: #3a3a3a;
    --icon: #141414;
    --button-bg: #2f2f2f;
  }
  * { box-sizing: border-box; margin: 0; padding: 0; }
  html, body { width: 800px; height: 1200px; overflow: hidden; background: var(--screen-bg); }
  body { font-family: "Ubuntu", sans-serif; color: var(--text); position: relative; }

  .status-bar { position: absolute; left: 0; top: 0; width: 800px; height: 50px; background: var(--status-bg); }
  .status-time { position: absolute; left: 0; right: 0; top: 6px; text-align: center; font-size: 30px; font-weight: 500; color: var(--status-fg); }
  .status-bar svg { position: absolute; }

  .nav-bar { position: absolute; left: 0; top: 50px; width: 800px; height: 110px;
    background: linear-gradient(var(--nav-top), var(--nav-bottom)); box-shadow: 0 4px 6px rgba(0,0,0,.45); z-index: 2; }
  .nav-title { position: absolute; left: 0; right: 0; top: 28px; text-align: center; font-size: 43px; font-weight: 700; }
  .nav-back { position: absolute; left: 20px; top: 19px; }
  .nav-back span { position: absolute; left: 35px; top: 20px; font-size: 28px; font-weight: 700; }
  .nav-done { position: absolute; right: 20px; top: 19px; width: 104px; height: 70px; border-radius: 8px;
    background: var(--nav-btn); border: 2px solid var(--nav-btn-edge); box-shadow: inset 0 2px 0 rgba(255,255,255,.15);
    font-size: 28px; font-weight: 700; text-align: center; line-height: 66px; }

  .row { position: absolute; left: 0; width: 800px; border-bottom: 2px solid var(--divider-dark); box-shadow: 0 2px 0 var(--divider-light); }
  .row-title { position: absolute; left: 107px; font-size: 34px; font-weight: 700; }
  .row-note { position: absolute; left: 107px; font-size: 24px; font-weight: 500; line-height: 32px; }
  .row-hint { position: absolute; left: 107px; font-size: 24px; color: var(--text-muted); }
  .row-icon, .chevron { position: absolute; }

  .toggle { position: absolute; left: 609px; width: 162px; height: 50px; border-radius: 9px; overflow: hidden;
    background: var(--toggle-off); box-shadow: inset 0 2px 4px rgba(0,0,0,.6); }
  .toggle-on { position: absolute; left: 0; top: 0; width: 81px; height: 50px; background: var(--toggle-on);
    border-radius: 9px 0 0 9px; text-align: center; line-height: 50px; font-size: 29px; font-weight: 700; }
  .toggle-off { position: absolute; right: 0; top: 0; width: 81px; height: 50px; text-align: center; line-height: 50px;
    font-size: 29px; font-weight: 700; color: var(--toggle-off-text); }

  .reset-button { position: absolute; left: 30px; top: 952px; width: 740px; height: 68px; border-radius: 8px;
    background: var(--button-bg); border: 2px solid var(--divider-dark); box-shadow: inset 0 2px 0 var(--divider-light);
    text-align: center; line-height: 64px; font-size: 34px; font-weight: 700; }
  .reset-hint { position: absolute; left: 0; right: 0; top: 1040px; text-align: center; font-size: 24px; color: var(--text-muted); }
</style>
</head>
<body>
  <header class="status-bar">
    <svg width="70" height="30" style="left:8px;top:10px" viewBox="0 0 70 30"><polygon points="0,28 60,2 60,28" fill="var(--status-fg)"/></svg>
    <div class="status-time">14:06 PM</div>
    <svg width="26" height="26" style="left:690px;top:12px" viewBox="0 0 26 26"><circle cx="13" cy="13" r="12" fill="var(--status-fg)"/><path d="M13 5v8h6" stroke="#000" stroke-width="3" fill="none"/></svg>
    <svg width="56" height="28" style="left:732px;top:11px" viewBox="0 0 56 28"><rect x="1.5" y="1.5" width="47" height="25" fill="none" stroke="var(--status-fg)" stroke-width="3"/><rect x="6" y="6" width="20" height="16" fill="var(--status-fg)"/><rect x="50" y="9" width="5" height="10" fill="var(--status-fg)"/></svg>
  </header>

  <nav class="nav-bar">
    <div class="nav-back">
      <svg width="124" height="72" viewBox="0 0 124 72"><path d="M22 2H116a6 6 0 0 1 6 6V64a6 6 0 0 1-6 6H22L2 36Z" fill="var(--nav-btn)" stroke="var(--nav-btn-edge)" stroke-width="2"/></svg>
      <span>Back</span>
    </div>
    <div class="nav-title">Settings</div>
    <div class="nav-done">Done</div>
  </nav>

  <section class="row" style="top:160px;height:128px">
    <svg class="row-icon" width="60" height="60" style="left:28px;top:34px" viewBox="0 0 60 60">
      <path d="M30 14C24 2 12 4 16 12c2 3 8 2 14 2c6 0 12 1 14-2c4-8-8-10-14 2Z" fill="none" stroke="var(--icon)" stroke-width="4"/>
      <rect x="2" y="16" width="56" height="14" fill="var(--icon)"/><rect x="6" y="32" width="48" height="26" fill="var(--icon)"/>
      <rect x="27" y="16" width="6" height="42" fill="var(--screen-bg)"/><rect x="6" y="36" width="48" height="5" fill="var(--screen-bg)"/>
    </svg>
    <div class="row-title" style="top:44px">Gift Kestrel Pix to a friend</div>
    <svg class="chevron" width="20" height="32" style="left:748px;top:48px" viewBox="0 0 20 32"><path d="M3 3l13 13L3 29" fill="none" stroke="var(--icon)" stroke-width="5"/></svg>
  </section>

  <section class="row" style="top:288px;height:128px">
    <svg class="row-icon" width="60" height="58" style="left:27px;top:34px" viewBox="0 0 60 58"><polygon points="30,4 37,22 56,22 41,34 46,53 30,42 14,53 19,34 4,22 23,22" fill="none" stroke="var(--icon)" stroke-width="5" stroke-linejoin="round"/></svg>
    <div class="row-title" style="top:44px">Rate / review in the Tundle Hub</div>
    <svg class="chevron" width="20" height="32" style="left:748px;top:48px" viewBox="0 0 20 32"><path d="M3 3l13 13L3 29" fill="none" stroke="var(--icon)" stroke-width="5"/></svg>
  </section>

  <section class="row" style="top:416px;height:230px">
    <svg class="row-icon" width="80" height="68" style="left:16px;top:40px" viewBox="0 0 80 68">
      <path d="M40 46C32 34 26 27 26 18a14 14 0 0 1 28 0c0 9-6 16-14 28Z" fill="var(--icon)"/><circle cx="40" cy="18" r="5" fill="var(--screen-bg)"/>
      <path d="M2 64L18 44H28M52 44H62L78 64L56 54L40 64L22 54Z" fill="none" stroke="var(--icon)" stroke-width="3" stroke-linejoin="round"/>
    </svg>
    <div class="row-title" style="top:48px">Geotagiing</div>
    <div class="toggle" style="top:45px"><div class="toggle-on">On</div><div class="toggle-off">Off</div></div>
    <div class="row-note" style="top:143px">Captured photos get location-specific<br>information</div>
    <div class="toggle" style="top:140px"><div class="toggle-on">On</div><div class="toggle-off">Off</div></div>
  </section>

  <section class="row" style="top:646px;height:88px">
    <div class="row-note" style="top:28px">Launch in Capture Mode</div>
    <div class="toggle" style="top:18px"><div class="toggle-on">On</div><div class="toggle-off">Off</div></div>
  </section>

  <section class="row" style="top:734px;height:158px">
    <div class="row-note" style="top:26px">Kestrel Pix is automatically lauched in<br>camera mode Autosave to Camera Roll</div>
    <div class="toggle" style="top:30px"><div class="toggle-on">On</div><div class="toggle-off">Off</div></div>
    <div class="row-hint" style="top:106px">Captured photos are directly saved to camera roll</div>
  </section>

  <div class="reset-button">Reset All Tutorials</div>
  <div class="reset-hint">Tap to reset all the tutorials</div>
</body>
</html>
```